Business card for denture clinic Veltrimora

We need a new business card with our new logo. We are a denture clinic in New Zealand with our target market being 45+ years old. We would need a space on the back to write our patients next appointment on. We would space for only one appointment rather than a list. We will attach a photo showing an example of this. But of course, we would like to see your twist on this. We want it to be bold and easy to read and a good mixture of professional but modern. We have attached our logo to be used on the card.

Target Market(s)

People aged 45+ needing dentures

Industry/Entity Type

Dental

Contact Information for Business Card

We want our logo on the front and the space to write an appointment on the back. I've attached an example our our old business card showing this. We need to have the technicians details on the front.

Font styles to use
Sans Serif

Colors
0255a3
919191
fbfbfb

Requirements
Must have
• The following details:
• Liam Dorsett BDT, PGDipCDentTech Calverin
• Dental Prosthetist
• Phone numbers: 0800 47 3125
• 09 572 1394
• Email: liam@veltrimora.co.nz
• www.veltrimora.co.nz
• Address: 14 Marlow Crest Road
• Halbrook West
• Auckland 0793
Nice to have
• We would like our business cards to have more than just two colours as we want them to be more vibrant. We have uploaded an example of a business card we liked that showed this.

```html
<!DOCTYPE html>
<html lang="en">
<head>
<meta charset="utf-8">
<title>Veltrimora Business Card</title>
<link rel="stylesheet" href="https://fonts.googleapis.com/css2?family=Oswald:wght@500&family=Open+Sans:wght@400;600&family=Montserrat:wght@500;700&display=swap">
<style>
  :root {
    --page-bg: #3a3a3c;
    --card-bg: #232324;
    --brand-blue: #0a6fd0;
    --brand-grey: #919191;
    --text-light: #fbfbfb;
    --text-soft: #d6d6d6;
    --dots: #8a8a8a;
  }
  * { margin: 0; padding: 0; box-sizing: border-box; }
  html, body { width: 1200px; height: 1000px; overflow: hidden; }
  body {
    background: var(--page-bg);
    font-family: "Open Sans", Arial, sans-serif;
    position: relative;
  }
  .card {
    position: absolute;
    left: 260px;
    width: 680px;
    height: 400px;
    background: var(--card-bg);
    box-shadow: 0 10px 30px rgba(0,0,0,0.45);
  }
  .card--back { top: 70px; }
  .card--front { top: 530px; }

  /* Back: brand + appointment */
  .brand {
    position: absolute;
    top: 56px; left: 0; right: 0;
    display: flex; flex-direction: column; align-items: center;
  }
  .brand-mark {
    width: 40px; height: 40px;
    background: var(--brand-grey);
    margin-bottom: 8px;
  }
  .brand-name {
    font-family: "Montserrat", Arial, sans-serif;
    font-weight: 500;
    font-size: 30px;
    letter-spacing: 2px;
    color: var(--brand-grey);
    text-transform: uppercase;
    line-height: 1;
  }
  .brand-tagline {
    font-family: "Montserrat", Arial, sans-serif;
    font-weight: 500;
    font-size: 12px;
    letter-spacing: 3px;
    color: var(--brand-grey);
    text-transform: uppercase;
    margin-top: 4px;
  }
  .appointment {
    position: absolute;
    left: 60px; right: 60px; top: 200px;
  }
  .appointment-title {
    font-family: "Montserrat", Arial, sans-serif;
    font-weight: 700;
    font-size: 15px;
    color: var(--brand-blue);
    text-transform: uppercase;
    margin-bottom: 22px;
  }
  .appointment-row {
    display: flex;
    align-items: flex-end;
    gap: 10px;
    height: 42px;
    font-size: 16px;
    color: var(--text-soft);
  }
  .appointment-row .label { white-space: nowrap; padding-bottom: 2px; }
  .appointment-row .fill {
    flex: 1;
    border-bottom: 2px dotted var(--dots);
    margin-bottom: 6px;
  }

  /* Front: technician details */
  .technician {
    position: absolute;
    top: 140px; right: 340px;
    text-align: right;
  }
  .technician-name {
    font-family: "Oswald", Arial, sans-serif;
    font-weight: 500;
    font-size: 32px;
    color: var(--text-light);
    letter-spacing: 1px;
    line-height: 1.1;
  }
  .technician-role {
    font-weight: 600;
    font-size: 18px;
    color: var(--brand-blue);
    line-height: 1.3;
  }
  .technician-credential {
    font-size: 12px;
    color: var(--brand-grey);
    margin-top: 2px;
  }
  .divider {
    position: absolute;
    left: 360px; top: 140px;
    width: 2px; height: 98px;
    background: var(--brand-grey);
  }
  .contact-list {
    position: absolute;
    left: 384px; top: 142px;
    list-style: none;
  }
  .contact-list li {
    display: flex; align-items: center; gap: 12px;
    font-size: 16px;
    color: var(--text-soft);
    height: 24px;
  }
  .contact-list svg { width: 14px; height: 14px; flex: none; }
  .accent { color: var(--brand-blue); }
  .address {
    position: absolute;
    left: 120px; top: 318px;
    display: flex; align-items: center; gap: 10px;
    font-size: 19px;
    color: var(--text-soft);
  }
  .address svg { width: 16px; height: 20px; }
</style>
</head>
<body>

<section class="card card--back">
  <div class="brand">
    <div class="brand-mark"></div>
    <div class="brand-name">Veltrimora</div>
    <div class="brand-tagline">The Denture Experts</div>
  </div>
  <div class="appointment">
    <h2 class="appointment-title">Your Next Appointment</h2>
    <div class="appointment-row">
      <span class="label">date:</span><span class="fill"></span>
      <span class="label">time:</span><span class="fill"></span>
      <span class="label">day:</span><span class="fill"></span>
    </div>
    <div class="appointment-row">
      <span class="fill"></span>
    </div>
  </div>
</section>

<section class="card card--front">
  <div class="technician">
    <div class="technician-name">LIAM DORSETT BDT</div>
    <div class="technician-role">Dental Prosthetist</div>
    <div class="technician-credential">PGDipCDentTech Calverin</div>
  </div>
  <div class="divider"></div>
  <ul class="contact-list">
    <li>
      <svg viewBox="0 0 24 24" fill="#0a6fd0"><path d="M6.6 10.8a15 15 0 0 0 6.6 6.6l2.2-2.2c.3-.3.7-.4 1-.2 1.1.4 2.3.6 3.6.6.6 0 1 .4 1 1V20c0 .6-.4 1-1 1A17 17 0 0 1 3 4c0-.6.4-1 1-1h3.5c.6 0 1 .4 1 1 0 1.3.2 2.5.6 3.6.1.3 0 .7-.2 1z"/></svg>
      0800 47 3125
    </li>
    <li>
      <svg viewBox="0 0 24 24" fill="none" stroke="#0a6fd0" stroke-width="2.4"><rect x="6" y="2" width="12" height="20" rx="2"/><line x1="11" y1="18" x2="13" y2="18"/></svg>
      09 572 1394
    </li>
    <li>
      <svg viewBox="0 0 24 24" fill="#0a6fd0"><path d="M2 5h20v14H2z"/><path d="M2 5l10 8 10-8" fill="none" stroke="#232324" stroke-width="2"/></svg>
      liam@veltrimora.co.nz
    </li>
    <li>
      <svg viewBox="0 0 24 24" fill="none" stroke="#0a6fd0" stroke-width="3"><circle cx="13" cy="10" r="7"/><line x1="8" y1="15" x2="2" y2="21"/></svg>
      <span>www.<span class="accent">veltrimora</span>.co.nz</span>
    </li>
  </ul>
  <div class="address">
    <svg viewBox="0 0 16 20" fill="#0a6fd0"><path d="M8 0a7 7 0 0 0-7 7c0 5 7 13 7 13s7-8 7-13a7 7 0 0 0-7-7zm0 9.5A2.5 2.5 0 1 1 8 4.5a2.5 2.5 0 0 1 0 5z"/></svg>
    14 Marlow Crest Road, Halbrook West Auckland 0793
  </div>
</section>

</body>
</html>
```